Bram Keystone Homes needs a business card

We need a business card for a new company in Canada, Ontario. Our company is all about luxury contraction homes for our clients. Our product and services are custom projects design. Under the business logo that will be created, we want a slogan that will be a memorable phrase for consumers to remember us to tell their friends and relatives.

Additional infomation
- Ludovic Entrasse
- President / Ceo
-519.604.3087

Find point what luxury construction products and services can be done

We like to see colors:
- #663300
- and something other colors or color that would attract the client needs and wants

The final design should communicate leads from new or old clients that will grow our empire. Most of all, we try to work among the budget that clients want

NOTE
- we also need an icon for the business (Example: Instagram, Facebook, and Whatsapp icons)
- We want the company name to be remembered easily for clients and our distributors who would get our orders.
- we need an icon on the business cards: Facebook and Instagram.

Thanks,
Bram Keystone Homes

```html
<!DOCTYPE html>
<html lang="en">
<head>
<meta charset="utf-8">
<title>Bram Keystone Homes – Business Card</title>
<link rel="stylesheet" href="https://fonts.googleapis.com/css2?family=Poppins:wght@400;600&family=Roboto+Condensed:wght@700&display=swap">
<style>
  :root {
    --brown: #663300;
    --ink: #4a4a4a;
    --card: #ffffff;
    --backdrop: #e9e6e2;
  }
  * { margin: 0; padding: 0; box-sizing: border-box; }
  html, body { width: 1200px; height: 874px; overflow: hidden; }
  body {
    background: var(--backdrop);
    position: relative;
    font-family: "Poppins", sans-serif;
  }
  .card {
    position: absolute;
    left: 250px;
    width: 700px;
    height: 400px;
    background: var(--card);
    box-shadow: 0 4px 18px rgba(0,0,0,0.12);
    overflow: hidden;
  }
  .card--front { top: 22px; }
  .card--back { top: 452px; }

  .brand { color: var(--brown); }
  .brand__name {
    font-family: "Poppins", sans-serif;
    font-weight: 600;
    letter-spacing: -0.5px;
    line-height: 1;
  }
  .brand__tagline {
    font-family: "Roboto Condensed", sans-serif;
    font-weight: 700;
    text-transform: uppercase;
    line-height: 1;
    white-space: nowrap;
  }

  .card--front .brand {
    position: absolute;
    left: 0; right: 0; top: 128px;
    text-align: center;
  }
  .card--front .brand__name { font-size: 50px; }
  .card--front .brand__tagline { font-size: 19px; margin-top: 12px; }

  .social {
    position: absolute;
    left: 0; right: 0; top: 300px;
    display: flex;
    justify-content: center;
    gap: 6px;
  }

  .card--back .brand {
    position: absolute;
    left: 40px; top: 40px;
  }
  .card--back .brand__name { font-size: 30px; }
  .card--back .brand__tagline { font-size: 12px; margin-top: 7px; }

  .contact {
    position: absolute;
    right: 70px; bottom: 56px;
    text-align: right;
  }
  .contact__name { color: var(--brown); font-size: 27px; font-weight: 400; line-height: 1.2; }
  .contact__role { color: var(--ink); font-size: 21px; line-height: 1.25; }
  .contact__phone { color: var(--ink); font-size: 18px; line-height: 1.4; }

  .accent-bar {
    position: absolute;
    right: 0; bottom: 30px;
    width: 22px; height: 86px;
    background: var(--brown);
  }
</style>
</head>
<body>
  <section class="card card--front">
    <div class="brand">
      <div class="brand__name">Bram Keystone Homes</div>
      <div class="brand__tagline">- Home Renovations - Custom Project Design -</div>
    </div>
    <div class="social" aria-label="Social media">
      <svg width="30" height="30" viewBox="0 0 30 30" role="img" aria-label="Social media link"><circle cx="15" cy="15" r="13.5" fill="none" stroke="#663300" stroke-width="1.5"/></svg>
      <svg width="30" height="30" viewBox="0 0 30 30" role="img" aria-label="Social media link"><circle cx="15" cy="15" r="13.5" fill="none" stroke="#663300" stroke-width="1.5"/></svg>
      <svg width="30" height="30" viewBox="0 0 30 30" role="img" aria-label="Messaging link"><circle cx="15" cy="15" r="13.5" fill="none" stroke="#663300" stroke-width="1.5"/></svg>
    </div>
  </section>

  <section class="card card--back">
    <div class="brand">
      <div class="brand__name">Bram Keystone Homes</div>
      <div class="brand__tagline">- Home Renovations - Custom Project Design -</div>
    </div>
    <div class="contact">
      <div class="contact__name">Ludovic Entrasse</div>
      <div class="contact__role">President / Ceo</div>
      <div class="contact__phone">519.604.3087</div>
    </div>
    <div class="accent-bar"></div>
  </section>
</body>
</html>
```